Lumo Organic Baby Wipes for retail sales into supermarkets

Design a new Organic Baby Wipes Pack that has a similar feel and details to the attachments under the Brand Name LUMO Organics. Please keep all writing in English and highlight the following info on the Pack. - 80 Pack, 100% Biodegradable,
Aloe Vera, Chamomile,Natural Vitamin E to soothe baby's skin.
Hypo Allergenic, pH Balanced for baby's skin.
Fragrance Free, Alcohol Free, Chlorine Free, Parabens Free.

Target Market(s)

Mums looking for a Organic Baby Wipe

Industry/Entity Type

Baby

Font styles to use
Sans Serif

Colors
9bcb3c
abd036
cadf82
ffffff

Requirements
Must have
• Lumo Organics, White Base, majority green writing with different shades, touches of Brown to represent Bamboo Wipes.
• Please make ORGANIC writing very big.
Nice to have
• Natural Organic feel going to use matt packaging.
Should not have
• Cluttered too much information

```html
<!DOCTYPE html>
<html lang="en">
<head>
<meta charset="utf-8">
<title>Lumo Organic Baby Wipes – Pack Label</title>
<link href="https://fonts.googleapis.com/css2?family=Coustard:wght@900&family=Pathway+Gothic+One&family=Roboto+Condensed:wght@700&display=swap" rel="stylesheet">
<style>
  :root {
    --green-leaf: #8cc43f;
    --green-lime: #9bcb3c;
    --green-bright: #abd036;
    --green-pale: #cadf82;
    --green-deep: #3f6b22;
    --green-band: #7db83a;
    --brown-bamboo: #7a5326;
    --ink: #2b2b2b;
    --white: #ffffff;
    --stage: #eef5e6;
  }
  * { margin: 0; padding: 0; box-sizing: border-box; }
  html, body { width: 1200px; height: 900px; overflow: hidden; }
  body { background: var(--stage); position: relative; }

  .label {
    position: absolute; left: 40px; top: 202px;
    width: 976px; height: 432px;
    transform: scale(1.1475); transform-origin: top left;
    background: linear-gradient(180deg, #eef6d8 0%, var(--white) 25%, var(--white) 100%);
    overflow: hidden;
    box-shadow: 0 4px 12px rgba(0,0,0,.15);
  }

  .hero-photo {
    position: absolute; left: 520px; top: 0; width: 456px; height: 348px;
    background:
      linear-gradient(90deg, var(--white) 0%, rgba(255,255,255,0) 22%),
      radial-gradient(ellipse at 40% 50%, #f3d3c0 0%, #e8b99c 40%, #c98d6a 70%, #8a5a3c 100%);
  }

  .brand-name {
    position: absolute; left: 100px; top: 22px;
    font-family: "Coustard", serif; font-weight: 900;
    font-size: 72px; line-height: 1; color: var(--green-leaf);
  }
  .title-organic {
    position: absolute; left: 66px; top: 134px;
    font-family: "Coustard", serif; font-weight: 900;
    font-size: 47px; letter-spacing: 1px; line-height: 1; color: var(--brown-bamboo);
  }
  .title-wipes {
    position: absolute; left: 68px; top: 194px;
    font-family: "Coustard", serif; font-weight: 900;
    font-size: 40px; line-height: 1; color: var(--green-deep);
  }

  .benefits-band {
    position: absolute; left: 0; top: 273px; width: 440px; height: 122px;
    background: linear-gradient(90deg, var(--green-band) 0%, var(--green-lime) 55%, rgba(202,223,130,.6) 80%, rgba(255,255,255,0) 100%);
  }
  .benefits-text {
    position: absolute; left: 84px; top: 279px;
    font-family: "Pathway Gothic One", sans-serif;
    font-size: 17px; line-height: 22px; color: var(--ink);
  }

  .pack-badge { position: absolute; left: 392px; top: 78px; width: 130px; height: 150px; }
  .origin-badge { position: absolute; left: 420px; top: 300px; width: 70px; height: 70px; }

  .tagline-band {
    position: absolute; left: 645px; top: 349px; width: 331px; height: 40px;
    background: linear-gradient(90deg, rgba(255,255,255,0) 0%, var(--green-lime) 30%, var(--green-band) 100%);
  }
  .tagline {
    position: absolute; right: 46px; top: 356px;
    font-family: "Pathway Gothic One", sans-serif;
    font-size: 22px; line-height: 26px; color: var(--white);
  }

  .base-band {
    position: absolute; left: 0; top: 395px; width: 976px; height: 37px;
    background: linear-gradient(180deg, var(--white) 0%, var(--green-pale) 55%, #e4efbf 100%);
  }
</style>
</head>
<body>
  <section class="label">
    <div class="hero-photo" role="img" aria-label="Photo of a smiling baby lying on its tummy being kissed on the cheek by its mother"></div>

    <div class="brand-name">Lumo</div>
    <div class="title-organic">ORGANIC</div>
    <div class="title-wipes">Baby Wipes</div>

    <div class="benefits-band"></div>
    <p class="benefits-text">
      Aloe Vera, Chamomile, Natural Vitamin E<br>
      to soothe baby's skin, Hypo Allergenic,<br>
      PH Balanced for baby's skin.<br>
      Fragrance Free, Alcohol Free,<br>
      Chlorine Free, Parabens Free.
    </p>

    <svg class="pack-badge" viewBox="0 0 130 150" aria-label="80 Pack, 100% Biodegradable">
      <defs>
        <path id="pack-arc" d="M14 60 Q65 8 116 60"/>
      </defs>
      <text font-family="Roboto Condensed, sans-serif" font-weight="700" font-size="19" fill="#3f6b22" text-anchor="middle">
        <textPath href="#pack-arc" startOffset="50%">80 ★ Pack</textPath>
      </text>
      <polygon points="65,44 113,72 113,126 65,154 17,126 17,72" fill="#8cc43f" transform="translate(0,-6)"/>
      <text x="65" y="104" text-anchor="middle" font-family="Roboto Condensed, sans-serif" font-weight="700" font-size="30" fill="#ffffff">100%</text>
      <text x="65" y="123" text-anchor="middle" font-family="Roboto Condensed, sans-serif" font-weight="700" font-size="12.5" fill="#ffffff">Biodegradable</text>
    </svg>

    <svg class="origin-badge" viewBox="0 0 70 70" aria-label="Company origin badge">
      <circle cx="35" cy="35" r="30" fill="none" stroke="#8cc43f" stroke-width="3"/>
    </svg>

    <div class="tagline-band"></div>
    <div class="tagline">Gentle By Nature</div>

    <div class="base-band"></div>
  </section>
</body>
</html>
```